Optometrist A5 flyer update 2014

We are an optical / optometrist business needing an existing A5 flyer updated. This flyer has been very successful but needs to be renewed.
We are supplying all the original source files including images.
I have included pdf files with annotations on the alteration we would like made.
We are open to suggestions / alterations to the design of the pamphlet.
We are after a modern design appealing to the various ages of our patient base.

```html
<!DOCTYPE html>
<html lang="en">
<head>
<meta charset="utf-8">
<title>Marlow Lane Optical – FAQ Flyer</title>
<link rel="stylesheet" href="https://fonts.googleapis.com/css2?family=Fira+Sans:ital,wght@0,300;0,400;0,600;0,700;1,600&display=swap">
<style>
  :root {
    --brand-blue: #17208f;
    --brand-green: #0b9a2f;
    --ink: #1c1c1c;
    --white: #ffffff;
    --photo-teal: #bfe0dc;
    --photo-mist: #e8f2f0;
    --photo-hair: #8c5a38;
    --photo-skin: #e7bc9c;
    --photo-shirt: #f4f1ee;
    --frame-black: #1f1f24;
    --frame-navy: #1d2a78;
  }
  * { margin: 0; padding: 0; box-sizing: border-box; }
  html, body { width: 846px; height: 1200px; overflow: hidden; background: var(--white); }
  body { font-family: "Fira Sans", sans-serif; color: var(--ink); }

  .flyer { position: relative; width: 846px; height: 1200px; overflow: hidden; background: var(--white); }

  .hero-photo {
    position: absolute; left: 0; top: 0; width: 846px; height: 480px;
    background:
      radial-gradient(ellipse 150px 190px at 590px 200px, var(--photo-skin) 0%, var(--photo-skin) 45%, rgba(231,188,156,0) 100%),
      radial-gradient(ellipse 260px 300px at 600px 200px, var(--photo-hair) 0%, var(--photo-hair) 55%, rgba(140,90,56,0) 100%),
      radial-gradient(ellipse 330px 110px at 560px 470px, var(--photo-shirt) 0%, rgba(244,241,238,0) 100%),
      linear-gradient(90deg, var(--photo-teal) 0%, var(--photo-mist) 35%, #f3efea 60%, #e9efee 100%);
  }
  .hero-fade {
    position: absolute; left: 0; top: 390px; width: 366px; height: 90px;
    background: linear-gradient(180deg, rgba(255,255,255,0) 0%, var(--white) 100%);
  }

  .brand-name {
    position: absolute; left: 58px; top: 266px;
    font-weight: 400; font-size: 36px; line-height: 1.15;
    color: var(--brand-blue);
  }

  .frame-shot {
    position: absolute; display: block; border-radius: 30px 30px 40px 40px;
    background: linear-gradient(90deg, rgba(31,31,36,0.25) 0%, var(--frame-black) 20%, var(--frame-black) 80%, rgba(31,31,36,0.25) 100%);
  }
  .frame-shot.half-rim { left: 60px; top: 548px; width: 266px; height: 72px; }
  .frame-shot.full-rim { left: 58px; top: 646px; width: 280px; height: 82px;
    background: linear-gradient(90deg, rgba(29,42,120,0.3) 0%, var(--frame-navy) 20%, var(--frame-black) 55%, var(--frame-navy) 80%, rgba(29,42,120,0.3) 100%); }
  .frame-shot.semi-rimless { left: 66px; top: 764px; width: 228px; height: 46px; }

  .hours-heading {
    position: absolute; left: 0; top: 848px; width: 366px; height: 64px;
    background: var(--brand-green); color: var(--white);
    font-weight: 700; font-size: 37px; line-height: 64px; padding-left: 50px;
  }
  .hours-table {
    position: absolute; left: 50px; top: 924px;
    border-collapse: collapse; font-weight: 600; font-size: 18px; color: var(--ink);
  }
  .hours-table td { height: 26px; padding: 0; }
  .hours-table .day { width: 140px; }

  .faq-heading {
    position: absolute; left: 366px; top: 480px; width: 480px; height: 74px;
    background: var(--brand-blue); color: var(--white);
    font-weight: 300; font-size: 31px; line-height: 74px; padding-left: 30px;
  }
  .faq-panel {
    position: absolute; left: 366px; top: 554px; width: 480px; height: 548px;
    background: var(--brand-green); color: var(--white);
  }
  .faq-item { position: absolute; left: 53px; width: 370px; font-size: 16px; line-height: 1.3; }
  .faq-item .question { font-weight: 600; font-style: italic; }
  .faq-item .answer { font-weight: 400; }
  .faq-item .marker { position: absolute; left: -21px; top: 3px; }
  .faq-item.first { top: 30px; }
  .faq-item.second { top: 190px; }
  .faq-item.third { top: 372px; }
  .faq-divider { position: absolute; left: 53px; width: 362px; height: 1px; background: var(--white); }
  .faq-divider.one { top: 170px; }
  .faq-divider.two { top: 351px; }

  .site-footer {
    position: absolute; left: 0; top: 1102px; width: 846px; height: 98px;
    background: var(--brand-blue); color: var(--white);
    text-align: center; font-weight: 600; font-size: 29px; line-height: 98px;
  }
</style>
</head>
<body>
<div class="flyer">
  <div class="hero-photo" role="img" aria-label="Photo of a smiling woman with brown hair wearing black rectangular glasses"></div>
  <div class="hero-fade"></div>

  <div class="brand-name">Marlow Lane<br>Optical</div>

  <span class="frame-shot half-rim" role="img" aria-label="Product photo of black half-rim spectacle frames"></span>
  <span class="frame-shot full-rim" role="img" aria-label="Product photo of black and blue full-rim spectacle frames"></span>
  <span class="frame-shot semi-rimless" role="img" aria-label="Product photo of black semi-rimless spectacle frames"></span>

  <div class="hours-heading">Opening Hours</div>
  <table class="hours-table">
    <tr><td class="day">Monday</td><td>9.00am - 5.30pm</td></tr>
    <tr><td class="day">Tuesday</td><td>9.00am - 6.30pm</td></tr>
    <tr><td class="day">Wednesday</td><td>9.00am - 5.30pm</td></tr>
    <tr><td class="day">Thursday</td><td>9.00am - 6.30pm</td></tr>
    <tr><td class="day">Friday</td><td>9.00am - 5.30pm</td></tr>
    <tr><td class="day">Saturday</td><td>9.00am - 1.00pm</td></tr>
  </table>

  <div class="faq-heading">Frequently Asked Questions</div>
  <div class="faq-panel">
    <div class="faq-item first">
      <svg class="marker" width="9" height="14" viewBox="0 0 9 14"><path d="M0 0 L9 7 L0 14 Z" fill="#ffffff"/></svg>
      <p class="question">Can I have fashion sunglasses made to my prescription?</p>
      <p class="answer">Yes. It does depend on the sunglasses and your prescription.<br>We offer a range of sunglasses that can be fitted with prescription lenses.</p>
    </div>
    <div class="faq-divider one"></div>
    <div class="faq-item second">
      <svg class="marker" width="9" height="14" viewBox="0 0 9 14"><path d="M0 0 L9 7 L0 14 Z" fill="#ffffff"/></svg>
      <p class="question">If I want new prescription lenses fitted to my existing pair of glasses, do I have to go without them for a week?</p>
      <p class="answer">No. We can usually fit new lenses to your own frame onsite.<br>You only need to be without your glasses for a few hours.</p>
    </div>
    <div class="faq-divider two"></div>
    <div class="faq-item third">
      <svg class="marker" width="9" height="14" viewBox="0 0 9 14"><path d="M0 0 L9 7 L0 14 Z" fill="#ffffff"/></svg>
      <p class="question">Do I have to purchase my spectacles where my private health fund directs?</p>
      <p class="answer">No. It is your decision where to have your eyes tested and where to purchase your spectacles or contact lenses. We can direct bill your private health fund with the ClaimPoint system.</p>
    </div>
  </div>

  <div class="site-footer">www.marlowlaneoptical.com.au</div>
</div>
</body>
</html>
```